Contemporary Business card for Event Manager

Needed for my startup events company in Melbourne. Events I manage will be based within the fashion industry, sporting events, product launches etc. Not weddings or small dinner parties. Therfore I am after something professional and aimed at high end corporate market; but with the added emphasis on not being too conservative or boring. I am happy with a pop of colour e.g. yellow or copper foil.

Target Market(s)

fashion industry, design industry, high end sporting events e.g. Polo, Grand Prix, corporate clients,

Industry/Entity Type

Fashion

Contact Information for Business Card

side 1
Lucy Brandt (can be upper or lower case, have a feature full stop between first and surname, or at the end of the nameetc) I am open to ideas. I would also be fine with my initials or name as a logo on the front (if this is the case my full name would need to go on the second side of the card.
2nd side:
Mobile: +61 400 817 263
email: lucy.brandt@mailnest.com.au

on one side of the card:
event management | brand activation | Advisory Services

Font styles to use
Serif
Sans Serif

Requirements
Must have
• side 2 must have
• mobile number
• email address
• event management | brand activation | Advisory Services
• ** my full name (Lucy Brandt) must be on the card somewhere)
Nice to have
• 1st side
• I see the card stock being either a dark grey, light grey, natural white or black (all matt colours on unprocessed card). I see the writing being copper foil, or foil white or foil black.
• To give you a feel for me, think: contemporary, minimalist, I love line drawings, concrete, white with grey vein marble, copper, white, grey, black...yes I do like colour....yellow (but pops of colour) ;) I would like the card to look designer but 'on trend' as I deal with a lot of design and fashion clients....styles - think the sophistication and simplicity of Vireaux or urban contemporary.
• some examples of what I like. Although please don't leet this limit you...I really am happy to have something a little more urban or design focused like a line drawing of an object, person too or a photo image too.
• https://www.moodtackle.com/pin/830165427719302846/
• https://www.moodtackle.com/pin/607281935540173268/
• https://www.moodtackle.com/pin/318746205913457092/
• https://www.moodtackle.com/pin/41983627530918476/
• https://www.moodtackle.com/pin/53128940672419087/
• https://www.moodtackle.com/pin/90316284750638152/
• https://www.moodtackle.com/pin/734092618450362918/
• https://www.moodtackle.com/pin/926354081736215407/
• https://www.moodtackle.com/pin/481627093518704356/
Should not have
• should not look commercial or have cartoonish looking logos. However happy with a simple line drawing or logo with initials etc.

```html
<!DOCTYPE html>
<html lang="en">
<head>
<meta charset="utf-8">
<title>Lucy Brandt — Business Card</title>
<link rel="stylesheet" href="https://fonts.googleapis.com/css2?family=Mulish:wght@400;700&display=swap">
<style>
  :root {
    --backdrop: #e9e7e4;
    --card-light: #ffffff;
    --card-dark: #232323;
    --ink: #111111;
    --emboss: #3b3b3b;
  }
  * { margin: 0; padding: 0; box-sizing: border-box; }
  html, body {
    width: 1200px; height: 1000px; overflow: hidden;
    background: var(--backdrop);
    font-family: "Mulish", "Century Gothic", sans-serif;
    color: var(--ink);
  }
  .canvas { position: relative; width: 1200px; height: 1000px; }
  .card { position: absolute; left: 265px; width: 666px; height: 397px; }
  .card--front { top: 73px; background: var(--card-light); }
  .card--back { top: 532px; background: var(--card-dark); }

  .front__name {
    position: absolute; top: 110px; left: 0; right: 0;
    text-align: center; font-weight: 700; font-size: 24px; line-height: 1.1;
  }
  .contact {
    position: absolute; left: 0; right: 0; text-align: center;
    font-size: 17px; font-weight: 400; line-height: 1.2;
  }
  .contact__icon { display: block; margin: 0 auto 1px; }
  .contact--phone { top: 154px; }
  .contact--email { top: 196px; }
  .services {
    position: absolute; top: 263px; left: 0; right: 0;
    text-align: center; font-size: 17.5px; letter-spacing: 0.2px; line-height: 1.2;
  }
  .services .sep { margin: 0 8px; }

  .back__mark {
    position: absolute; top: 128px; left: 0; right: 0;
    text-align: center; font-weight: 700; font-size: 50px; line-height: 1;
    color: var(--emboss);
  }
  .back__name {
    position: absolute; top: 278px; left: 0; right: 0;
    text-align: center; font-weight: 700; font-size: 29px; line-height: 1;
    color: var(--emboss); letter-spacing: 0.5px;
  }
</style>
</head>
<body>
<main class="canvas">
  <section class="card card--front" aria-label="Card front">
    <h1 class="front__name">Lucy Brandt</h1>
    <p class="contact contact--phone">
      <svg class="contact__icon" width="12" height="12" viewBox="0 0 12 12" aria-hidden="true">
        <path d="M2 10 C1 7 2 3 6 1.5 L8 1 L8.8 3 L6.8 3.8 C5 5 4.6 6.8 5 8.5 L7 8.6 L7.4 10.8 L5.2 11.2 C3.8 11.4 2.6 11 2 10 Z" fill="var(--ink)"/>
      </svg>
      +61 400 817 263
    </p>
    <p class="contact contact--email">
      <svg class="contact__icon" width="13" height="10" viewBox="0 0 13 10" aria-hidden="true">
        <rect x="0.5" y="0.5" width="12" height="9" fill="var(--ink)"/>
        <path d="M0.5 0.5 L6.5 5.5 L12.5 0.5" fill="none" stroke="#fff" stroke-width="1"/>
      </svg>
      lucy.brandt@mailnest.com.au
    </p>
    <p class="services">Event Management<span class="sep">|</span>Brand Activation<span class="sep">|</span>Advisory Services</p>
  </section>

  <section class="card card--back" aria-label="Card back">
    <p class="back__mark">Lucy Brandt</p>
    <p class="back__name">Lucy Brandt</p>
  </section>
</main>
</body>
</html>
```